WordPress Design for both website and landing page for an expert

I need a clean and stylish design for my new website. I work as an expert (see attached file WHY HOW WHAT), my product is expert opinion (reports) for company evaluations You can use all of the attached pictures colored or black / white. The person is me, you can add other pictures, if you want. The design should be clean and stylish, so you could use white, black, gray, silver and / or one additional color. I have added an idea about my website, see attached file CONCEPT WEBSITE If you have any more information, please do not hesitate to contact us 'Hesitate to ask me ...

```html
<!DOCTYPE html>
<html lang="en">
<head>
<meta charset="utf-8">
<title>Elias Marwen – Expert for company valuations</title>
<link rel="stylesheet" href="https://fonts.googleapis.com/css2?family=Montserrat:wght@400;500;600;700&family=Noto+Serif:wght@400&display=swap">
<style>
  :root {
    --ink: #1f2328;
    --ink-soft: #3a3f45;
    --muted: #8b95a0;
    --nav-active: #a4a9ae;
    --line: #c9cdd1;
    --band: #f0f3f6;
    --band-note: #f3f5f7;
    --white: #ffffff;
    --dark-dot: #33383e;
  }
  * { box-sizing: border-box; margin: 0; padding: 0; }
  html, body { width: 1200px; height: 2248px; overflow: hidden; }
  body {
    position: relative;
    background: var(--white);
    font-family: "Montserrat", Arial, sans-serif;
    color: var(--ink);
  }
  .abs { position: absolute; }

  /* Header */
  .brand {
    left: 68px; top: 38px; width: 184px;
    display: flex; flex-direction: column; align-items: center; gap: 14px;
  }
  .brand-dot { width: 34px; height: 34px; border-radius: 50%; background: var(--ink); }
  .brand-name {
    font-size: 17px; font-weight: 400; letter-spacing: 3.4px;
    color: var(--ink); white-space: nowrap;
  }
  .main-nav {
    top: 59px; left: 597px;
    display: flex; gap: 0;
    font-size: 13px; font-weight: 600; letter-spacing: 2px;
  }
  .main-nav a { position: absolute; white-space: nowrap; color: var(--ink); text-decoration: none; }
  .main-nav a.is-active { color: var(--nav-active); }

  /* Hero */
  .hero {
    left: 137px; top: 197px; width: 925px; height: 376px;
    background:
      linear-gradient(90deg, rgba(60,62,64,.0) 0%, rgba(60,62,64,.0) 100%),
      linear-gradient(90deg, #a9a39b 0%, #cfcac3 18%, #6f6c69 32%, #59585a 48%, #bfc3c4 60%, #e3e6e6 72%, #aeb6bb 84%, #d9dcd8 100%);
  }
  .hero-title {
    left: 137px; width: 925px; top: 342px; text-align: center;
    font-size: 43px; font-weight: 500; letter-spacing: 4px; color: var(--white);
  }
  .hero-sub {
    left: 137px; width: 925px; top: 396px; text-align: center;
    font-size: 16px; font-weight: 400; color: var(--white);
  }

  /* Intro */
  .intro {
    left: 282px; top: 638px; width: 640px;
    font-family: "Noto Serif", Georgia, serif;
    font-size: 14.5px; line-height: 25.5px; color: var(--muted);
  }

  .section-title {
    left: 0; width: 1200px; text-align: center;
    font-size: 27px; font-weight: 500; line-height: 39px; color: var(--ink);
  }

  /* Reasons timeline */
  .timeline-line { left: 599px; top: 876px; width: 2px; height: 516px; background: var(--line); }
  .step-icon {
    width: 70px; height: 70px; border-radius: 50%;
    border: 1.5px solid var(--line); background: var(--white);
    display: flex; align-items: center; justify-content: center;
  }
  .step-icon.is-filled { background: var(--dark-dot); border-color: var(--dark-dot); }
  .step { width: 250px; }
  .step.is-left { text-align: right; }
  .step-title {
    font-size: 16px; font-weight: 600; letter-spacing: 3.3px; color: var(--ink);
    margin-bottom: 7px;
  }
  .step-text {
    font-family: "Noto Serif", Georgia, serif;
    font-size: 14.5px; line-height: 25.5px; color: var(--muted);
  }

  /* Buying motives */
  .motives { left: 0; top: 1462px; width: 1200px; height: 365px; background: var(--band); }
  .motive { width: 300px; }
  .motive svg { position: absolute; left: 0; top: -44px; }
  .motive-text {
    position: relative;
    font-family: "Noto Serif", Georgia, serif;
    font-size: 14.5px; line-height: 25.5px; color: var(--muted);
  }
  .pager { top: 1773px; left: 583px; display: flex; gap: 8px; }
  .pager span { width: 11px; height: 11px; border-radius: 50%; border: 1.5px solid var(--ink-soft); }
  .pager span.is-current { background: radial-gradient(circle, var(--ink-soft) 0 2px, transparent 2.5px); }

  .note-band {
    left: 0; top: 1830px; width: 1200px; height: 68px;
    background: var(--band-note); border-top: 1px solid #e8ecef;
  }
  .note {
    left: 0; width: 1200px; top: 1851px; text-align: center;
    font-size: 10.5px; line-height: 17px; color: var(--muted);
  }
  .note strong { font-weight: 600; color: #6f7780; }

  /* Call to action */
  .cta-button {
    left: 493px; top: 2071px; width: 213px; height: 39px;
    border: 1.5px solid #b9bec3; border-radius: 20px;
    display: flex; align-items: center; justify-content: center;
    font-size: 13px; font-weight: 600; letter-spacing: 1px; color: var(--ink);
  }

  /* Footer */
  .site-footer { left: 0; top: 2180px; width: 1200px; height: 68px; background: var(--band); }
  .copyright { left: 137px; top: 2207px; font-size: 11px; color: #7c858e; }
  .social { top: 2194px; width: 40px; height: 40px; border-radius: 50%; background: var(--white); }
</style>
</head>
<body>

<header>
  <div class="brand abs">
    <span class="brand-dot"></span>
    <span class="brand-name">ELIAS MARWEN</span>
  </div>
  <nav class="main-nav abs">
    <a href="#" style="left:0">HOME</a>
    <a href="#" class="is-active" style="left:81px">ABOUT</a>
    <a href="#" style="left:169px">WHAT I DO</a>
    <a href="#" style="left:289px">WHY / HOW I DO</a>
    <a href="#" style="left:459px">CONTACT</a>
  </nav>
</header>

<main>
  <div class="hero abs" role="img" aria-label="Portrait of the expert in a dark suit standing in a bright office corridor"></div>
  <h1 class="hero-title abs">ELIAS MARWEN</h1>
  <p class="hero-sub abs">Expert for company valuations</p>

  <p class="intro abs">Sed ut perspiciatis unde omnis iste natus &nbsp;voluptatem accusantium doloremque laudantium, totam rem aperiam, eaque ipsa quae inventore veritatis et quasi architecto eaque ipsa beatae vitae dicta sunt explicabo.</p>

  <h2 class="section-title abs" style="top:766px">3 reasons, Why you should<br>work with me.</h2>

  <div class="timeline-line abs"></div>

  <div class="step-icon abs" style="left:565px;top:918px">
    <svg width="24" height="24" viewBox="0 0 24 24" fill="none" stroke="#3a3f45" stroke-width="1.6">
      <rect x="3" y="4.5" width="18" height="16" rx="1"/>
      <line x1="3" y1="9" x2="21" y2="9"/>
      <line x1="8" y1="2.5" x2="8" y2="6"/><line x1="16" y1="2.5" x2="16" y2="6"/>
      <path d="M7 12.5h2M11 12.5h2M15 12.5h2M7 16h2M11 16h2M15 16h2"/>
    </svg>
  </div>
  <div class="step abs" style="left:669px;top:922px">
    <h3 class="step-title">FAST PROCESS</h3>
    <p class="step-text">You will receive your report promptly (within a maximum of 21 days after receipt of all required documents)</p>
  </div>

  <div class="step-icon is-filled abs" style="left:565px;top:1073px">
    <svg width="26" height="26" viewBox="0 0 24 24" fill="none" stroke="#ffffff" stroke-width="1.5">
      <circle cx="12" cy="9" r="5.5"/>
      <path d="M8.5 13.5 6.5 20l3-1.5L11 21M15.5 13.5l2 6.5-3-1.5L13 21"/>
    </svg>
  </div>
  <div class="step is-left abs" style="left:277px;top:1076px">
    <h3 class="step-title">CERTIFIED</h3>
    <p class="step-text">You receive a qualified and reliable report from a certified expert (highest acceptance by all parties)</p>
  </div>

  <div class="step-icon abs" style="left:565px;top:1225px">
    <svg width="24" height="24" viewBox="0 0 24 24" fill="none" stroke="#3a3f45" stroke-width="1.6" stroke-linejoin="round">
      <rect x="3" y="10" width="4" height="10"/>
      <path d="M7 11 11 4c1.5 0 2.5 1 2 3l-1 3h6c1.2 0 2 1 1.8 2.2l-1.2 6c-.2 1-1 1.8-2 1.8H7"/>
    </svg>
  </div>
  <div class="step abs" style="left:669px;top:1232px">
    <h3 class="step-title">UNDERSTANDABLE</h3>
    <p class="step-text">Your report will be logical and comprehensible for you and will not contain any "technical Chinese"</p>
  </div>

  <section class="motives abs" aria-label="Buying motives"></section>
  <h2 class="section-title abs" style="top:1523px">What are the buying motives<br>of the customers?</h2>

  <div class="motive abs" style="left:282px;top:1659px">
    <svg width="52" height="48" viewBox="0 0 52 48" fill="none" stroke="#ffffff" stroke-width="3">
      <circle cx="24" cy="24" r="21"/>
      <path d="M13 24l9 9 24-26"/>
    </svg>
    <p class="motive-text">You want to transfer your business to your heirs and need a valuation for the tax office?</p>
  </div>
  <div class="motive abs" style="left:634px;top:1659px">
    <svg width="52" height="48" viewBox="0 0 52 48" fill="none" stroke="#ffffff" stroke-width="3">
      <circle cx="24" cy="24" r="21"/>
      <path d="M13 24l9 9 24-26"/>
    </svg>
    <p class="motive-text">You have to pay someone in the context of a separation / divorce and need a tax base?</p>
  </div>
  <div class="pager abs"><span class="is-current"></span><span></span></div>

  <div class="note-band abs"></div>
  <p class="note abs"><strong>Note:</strong> The cost of a report are always disproportionately cheaper than the cost of legal disputes.<br>And that detached from the psychological burden of such an argument ...</p>

  <h2 class="section-title abs" style="top:1959px">You need an opinion to determine<br>the value of your company</h2>
  <a class="cta-button abs" href="#">CONTACT NOW!</a>
</main>

<footer>
  <div class="site-footer abs"></div>
  <p class="copyright abs">Copyright © 2018 Elias Marwen. All Rights Reserved</p>
  <span class="social abs" style="left:917px" aria-label="Social profile"></span>
  <span class="social abs" style="left:968px" aria-label="Social profile"></span>
  <span class="social abs" style="left:1021px" aria-label="Social profile"></span>
</footer>

</body>
</html>
```